Internal web page of multinational company - Portfolio of reports

We need to improve the look & feel of an existing internal HTML page.
We use it as a portfolios where users go and see a list of existing reports as "tiles". The HTML page is automatically generated by a javascript that reads the contents to display from an HTML file.
What is needs is a "face lift" in the design of the page.
Currently we use icons on the top right of each tile to denote the type of technology used on the report and also colons for the same purpose. The attached screenshots will be self explanatory.
Across the top we have "tabs" that, once selected change the tiles.
Need a proposal for new design that keeps is as clean as possible, specially the home page that should be very light (Plimbo like).
The idea for this page is to serve as a "one stop shop" and become a bookmark for everyone in the company.
Looking for a wow effect that make is visually

Target Market(s)

Internal employees

Industry/Entity Type

It Company

Coding

Coded - Design and coding required

Number of Pages Required

2 page

Requirements
Must have
• Should not change the logo or its position from the bottom left.
• Page must be as clean as possible and
Nice to have
• Welcome to change the logo on the top left. This page is from the CSU M&I (Mni) which stands for Central Support Unit - Metrics & Insight.
Should not have
• Do no use red, this is the color of our competitor. The blue on the bottom is standard for our logo

```html
<!DOCTYPE html>
<html lang="en">
<head>
<meta charset="utf-8">
<title>Solutions Portfolio – Finance</title>
<link href="https://fonts.googleapis.com/css2?family=Roboto:wght@400;500;700&family=Roboto+Condensed:wght@400;700&family=Oswald:wght@400;500&display=swap" rel="stylesheet">
<style>
  :root{
    --page-bg:#f4f4f5;
    --card-bg:#fafafa;
    --brand-blue:#1b74c9;
    --link-blue:#1f6fc5;
    --navy:#0d2a78;
    --grey-square:#a9a9a9;
    --orange:#ef8a3c;
    --nav-text:#5a5a5a;
    --line:#d8d8d8;
    --tile-border:#d4d4d4;
    --icon:#444;
    --help:#ffa90a;
    --white:#ffffff;
  }
  *{box-sizing:border-box;margin:0;padding:0}
  html,body{width:1200px;height:594px;overflow:hidden;background:var(--page-bg);font-family:"Roboto",Arial,sans-serif}
  .portal{position:absolute;left:60px;top:31px;width:1080px;height:525px;background:var(--card-bg);border-radius:12px;overflow:hidden;box-shadow:0 1px 4px rgba(0,0,0,.12);border-top:7px solid var(--brand-blue)}
  .masthead{position:absolute;left:15px;right:15px;top:17px;height:71px;border-bottom:1px solid var(--line)}
  .unit-mark{position:absolute;left:0;top:0;display:flex;align-items:center;gap:6px}
  .unit-mark__dot{width:49px;height:49px;border-radius:50%;background:var(--navy)}
  .unit-mark__name{font-family:"Roboto Condensed",Arial,sans-serif;color:var(--navy);line-height:1.1}
  .unit-mark__name strong{display:block;font-size:15px;font-weight:700}
  .unit-mark__name span{display:block;font-size:15px;font-weight:400;color:var(--brand-blue)}
  .tabs{position:absolute;left:194px;top:20px;width:632px;display:flex;justify-content:space-between;list-style:none;font-family:"Roboto Condensed",Arial,sans-serif;font-size:13.5px;line-height:34px;color:var(--nav-text);text-transform:uppercase;white-space:nowrap}
  .tabs li{display:flex;align-items:center;gap:3px}
  .tabs .is-active{color:var(--brand-blue);font-weight:700}
  .tabs .filter{color:#222;font-weight:700}
  .search{position:absolute;left:842px;top:20px;width:178px;height:34px;border:1px solid var(--line);background:var(--white);display:flex;align-items:center;justify-content:space-between;padding:0 10px 0 14px;font-size:12px;color:#888}
  .close-btn{position:absolute;left:1018px;top:20px;width:32px;height:34px;border:1px solid var(--line);background:var(--white);display:flex;align-items:center;justify-content:center}
  .search{left:833px}
  .close-btn{left:1019px}
  .tiles{position:absolute;left:15px;top:144px;display:grid;grid-template-columns:repeat(4,251px);grid-auto-rows:57px;column-gap:16px;row-gap:18px}
  .tile{position:relative;border:2px solid var(--tile-border);background:var(--card-bg);border-radius:2px}
  .tile__head{position:absolute;left:4px;top:10px;display:flex;align-items:center;gap:2px;font-size:12.5px;letter-spacing:.2px;color:var(--link-blue);white-space:nowrap}
  .tile__head .sq{width:11px;height:11px;display:inline-block}
  .tile__head .sq--navy{background:var(--navy)}
  .tile__head .sq--orange{background:var(--orange)}
  .tile__head .sq--grey{background:var(--grey-square);margin-right:6px}
  .tile--orange .tile__head{color:var(--orange)}
  .tile__tech{position:absolute;right:6px;top:5px;width:16px;height:16px;background:#f1ece6;border:1px solid #e6e0da}
  .tile__actions{position:absolute;right:6px;bottom:6px;display:flex;gap:6px}
  .footer{position:absolute;left:0;right:0;bottom:0;height:48px;background:var(--brand-blue)}
  .help-btn{position:absolute;left:21px;top:9px;width:138px;height:28px;background:var(--help);border-radius:2px;display:flex;align-items:center;gap:8px;padding-left:12px;font-family:"Roboto Condensed",Arial,sans-serif;font-size:13px;color:var(--white)}
  .brand-name{position:absolute;right:14px;top:7px;font-family:"Oswald","Roboto Condensed",sans-serif;font-size:25px;font-weight:400;color:var(--white)}
</style>
</head>
<body>
<main class="portal">
  <header class="masthead">
    <div class="unit-mark">
      <span class="unit-mark__dot"></span>
      <div class="unit-mark__name"><strong>Solutions Portfolio</strong><span>Shared Services</span></div>
    </div>
    <ul class="tabs">
      <li class="is-active">Finance <svg width="8" height="6" viewBox="0 0 8 6"><path d="M1 1l3 3 3-3" fill="none" stroke="#1b74c9" stroke-width="1.2"/></svg></li>
      <li>GM View</li><li>Hub View</li><li>MI</li><li>General Accounting</li><li>Tax</li><li>Treasury</li><li>Knlowledge</li>
      <li class="filter">Filter <svg width="8" height="6" viewBox="0 0 8 6"><path d="M1 1l3 3 3-3" fill="none" stroke="#777" stroke-width="1.2"/></svg></li>
    </ul>
    <div class="search"><span>Search...</span>
      <svg width="16" height="16" viewBox="0 0 16 16"><circle cx="6" cy="6" r="4.2" fill="none" stroke="#333" stroke-width="1.6"/><path d="M9 9l5 5" stroke="#333" stroke-width="2.2"/></svg>
    </div>
    <div class="close-btn"><svg width="13" height="13" viewBox="0 0 13 13"><path d="M1 1l11 11M12 1L1 12" stroke="#555" stroke-width="1.3"/></svg></div>
  </header>

  <svg width="0" height="0" style="position:absolute">
    <defs>
      <symbol id="ic-wrench" viewBox="0 0 14 14"><path d="M2 12l6-6M8 6a3 3 0 1 0 3-4l-2 2 1 1 2-2a3 3 0 0 1-4 3" fill="none" stroke="#444" stroke-width="1.3"/></symbol>
      <symbol id="ic-doc" viewBox="0 0 14 14"><rect x="2" y="3" width="8" height="10" fill="none" stroke="#444"/><path d="M4 1h8v10" fill="none" stroke="#444"/><path d="M4 6h4M4 8h4M4 10h4" stroke="#444"/></symbol>
      <symbol id="ic-bars" viewBox="0 0 16 14"><path d="M1 13h15" stroke="#444"/><rect x="2" y="8" width="2" height="5" fill="none" stroke="#444" stroke-width=".9"/><rect x="6" y="6" width="2" height="7" fill="none" stroke="#444" stroke-width=".9"/><rect x="10" y="4" width="2" height="9" fill="none" stroke="#444" stroke-width=".9"/><rect x="13.5" y="1" width="2" height="12" fill="none" stroke="#444" stroke-width=".9"/></symbol>
    </defs>
  </svg>

  <section class="tiles">
    <article class="tile"><div class="tile__head"><span class="sq sq--navy"></span><span class="sq sq--grey"></span>B&amp;AT Revenu &amp; Margin Analysis</div><span class="tile__tech"></span><div class="tile__actions"><svg width="14" height="14"><use href="#ic-wrench"/></svg><svg width="14" height="14"><use href="#ic-doc"/></svg><svg width="16" height="14"><use href="#ic-bars"/></svg></div></article>
    <article class="tile tile--orange"><div class="tile__head"><span class="sq sq--orange"></span><span class="sq sq--grey"></span>BOLT</div><span class="tile__tech"></span><div class="tile__actions"><svg width="14" height="14"><use href="#ic-wrench"/></svg><svg width="14" height="14"><use href="#ic-doc"/></svg><svg width="16" height="14"><use href="#ic-bars"/></svg></div></article>
    <article class="tile"><div class="tile__head"><span class="sq sq--navy"></span><span class="sq sq--grey"></span>BSQ Dashboard</div><span class="tile__tech"></span><div class="tile__actions"><svg width="14" height="14"><use href="#ic-wrench"/></svg><svg width="14" height="14"><use href="#ic-doc"/></svg><svg width="16" height="14"><use href="#ic-bars"/></svg></div></article>
    <article class="tile"><div class="tile__head"><span class="sq sq--navy"></span><span class="sq sq--grey"></span>Global JV Trends</div><span class="tile__tech"></span><div class="tile__actions"><svg width="14" height="14"><use href="#ic-wrench"/></svg><svg width="14" height="14"><use href="#ic-doc"/></svg><svg width="16" height="14"><use href="#ic-bars"/></svg></div></article>

    <article class="tile"><div class="tile__head"><span class="sq sq--navy"></span><span class="sq sq--grey"></span>B&amp;AT Revenu &amp; Margin Analysis</div><span class="tile__tech"></span><div class="tile__actions"><svg width="14" height="14"><use href="#ic-wrench"/></svg><svg width="14" height="14"><use href="#ic-doc"/></svg><svg width="16" height="14"><use href="#ic-bars"/></svg></div></article>
    <article class="tile tile--orange"><div class="tile__head"><span class="sq sq--orange"></span><span class="sq sq--grey"></span>BOLT</div><span class="tile__tech"></span><div class="tile__actions"><svg width="14" height="14"><use href="#ic-wrench"/></svg><svg width="14" height="14"><use href="#ic-doc"/></svg><svg width="16" height="14"><use href="#ic-bars"/></svg></div></article>
    <article class="tile"><div class="tile__head"><span class="sq sq--navy"></span><span class="sq sq--grey"></span>BSQ Dashboard</div><span class="tile__tech"></span><div class="tile__actions"><svg width="14" height="14"><use href="#ic-wrench"/></svg><svg width="14" height="14"><use href="#ic-doc"/></svg><svg width="16" height="14"><use href="#ic-bars"/></svg></div></article>
    <article class="tile"><div class="tile__head"><span class="sq sq--navy"></span><span class="sq sq--grey"></span>Global JV Trends</div><span class="tile__tech"></span><div class="tile__actions"><svg width="14" height="14"><use href="#ic-wrench"/></svg><svg width="14" height="14"><use href="#ic-doc"/></svg><svg width="16" height="14"><use href="#ic-bars"/></svg></div></article>

    <article class="tile"><div class="tile__head"><span class="sq sq--navy"></span><span class="sq sq--grey"></span>B&amp;AT Revenu &amp; Margin Analysis</div><span class="tile__tech"></span><div class="tile__actions"><svg width="14" height="14"><use href="#ic-wrench"/></svg><svg width="14" height="14"><use href="#ic-doc"/></svg><svg width="16" height="14"><use href="#ic-bars"/></svg></div></article>
    <article class="tile tile--orange"><div class="tile__head"><span class="sq sq--orange"></span><span class="sq sq--grey"></span>BOLT</div><span class="tile__tech"></span><div class="tile__actions"><svg width="14" height="14"><use href="#ic-wrench"/></svg><svg width="14" height="14"><use href="#ic-doc"/></svg><svg width="16" height="14"><use href="#ic-bars"/></svg></div></article>
    <article class="tile"><div class="tile__head"><span class="sq sq--navy"></span><span class="sq sq--grey"></span>BSQ Dashboard</div><span class="tile__tech"></span><div class="tile__actions"><svg width="14" height="14"><use href="#ic-wrench"/></svg><svg width="14" height="14"><use href="#ic-doc"/></svg><svg width="16" height="14"><use href="#ic-bars"/></svg></div></article>
    <article class="tile"><div class="tile__head"><span class="sq sq--navy"></span><span class="sq sq--grey"></span>Global JV Trends</div><span class="tile__tech"></span><div class="tile__actions"><svg width="14" height="14"><use href="#ic-wrench"/></svg><svg width="14" height="14"><use href="#ic-doc"/></svg><svg width="16" height="14"><use href="#ic-bars"/></svg></div></article>

    <article class="tile"><div class="tile__head"><span class="sq sq--navy"></span><span class="sq sq--grey"></span>B&amp;AT Revenu &amp; Margin Analysis</div><span class="tile__tech"></span><div class="tile__actions"><svg width="14" height="14"><use href="#ic-wrench"/></svg><svg width="14" height="14"><use href="#ic-doc"/></svg><svg width="16" height="14"><use href="#ic-bars"/></svg></div></article>
    <article class="tile tile--orange"><div class="tile__head"><span class="sq sq--orange"></span><span class="sq sq--grey"></span>BOLT</div><span class="tile__tech"></span><div class="tile__actions"><svg width="14" height="14"><use href="#ic-wrench"/></svg><svg width="14" height="14"><use href="#ic-doc"/></svg><svg width="16" height="14"><use href="#ic-bars"/></svg></div></article>
  </section>

  <footer class="footer">
    <div class="help-btn">
      <svg width="20" height="16" viewBox="0 0 20 16"><path d="M10 1.5c4.4 0 8 2.6 8 5.8s-3.6 5.8-8 5.8c-.9 0-1.8-.1-2.6-.3L3 14.5l1.3-3C2.8 10.4 2 8.9 2 7.3 2 4.1 5.6 1.5 10 1.5z" fill="none" stroke="#fff" stroke-width="1.3"/></svg>
      Help &amp; Feedback
    </div>
    <div class="brand-name">Norvane</div>
  </footer>
</main>
</body>
</html>
```